Fahrzeugbeschriftung für Fahrschule gesucht
Ich bin sehr sehr zufrieden mit dem Ergebnis.Die wünsche die ich hatte wurden ohne zu zögern gleich umgesetzt. Der Designer arbeitet schnell und Präzise. Sehr gerne wieder für zukünftige Projekte!!
Zielgruppe
Meine Firma ist eine Fahrschule. Name der Fahrschule ist ZAP. Die Fahrschule befindet sich in Heidelberg am Neckar. Wir bilden alle Motorradklassen, PKW Klassen und Anhänger für PKW aus.
Unsere Zielgruppe sind hauptsächlich Jugendliche von 16-25 Jahren.
Aufgabenstellung
Unsere Fahrzeuge sind Schwarz, der Anhänger soll als Werbefläche für die Fahrschule dienen und soll auffallen. Das Grundelement des Designs sollte eher dunkel bleiben. Der Anhänger ist weiß und soll schwarz foliert bzw. Eure Ideen soll auf die Folie drauf und das auf den Anhänger.Ich bin Motorrad begeistert und brenne für meinen Job.
Ich möchte gerne mein Logo in Illustrationen einbauen. Das Logo soll bitte auch im Grafitti Stil sein
Hier ein link als Beispiele
https://www.bildkorbano.de/de/grafiken/graffiti-hintergrund?sort=best&mediatype=illustration&assetfiletype=eps&phrase=Graffiti%20Hintergrund

```html
<!DOCTYPE html>
<html lang="de">
<head>
<meta charset="utf-8">
<title>Fahrschule ZAP – Anhängerbeschriftung</title>
<link rel="stylesheet" href="https://fonts.googleapis.com/css2?family=Barlow+Condensed:ital,wght@0,700;1,700&family=Archivo:ital,wght@1,800&display=swap">
<style>
  :root {
    --page-bg: #e6e6e4;
    --wall-dark: #1f1f1f;
    --wall-mid: #353535;
    --wall-light: #444444;
    --chalk: #e4e4e2;
    --chalk-dim: #a9a9a7;
  }
  html, body {
    margin: 0;
    width: 1200px;
    height: 800px;
    overflow: hidden;
    background: var(--page-bg);
  }
  .canvas {
    position: relative;
    width: 1200px;
    height: 800px;
  }
  .trailer-wrap {
    position: absolute;
    left: 278px;
    top: 20px;
    width: 644px;
    height: 760px;
    overflow: hidden;
  }
  .wall-texture {
    position: absolute;
    inset: 0;
    background: radial-gradient(ellipse at 40% 30%, var(--wall-light) 0%, var(--wall-mid) 45%, var(--wall-dark) 100%);
  }
  .brand {
    position: absolute;
    left: 0;
    right: 0;
    top: 130px;
    display: flex;
    align-items: center;
    justify-content: center;
    gap: 16px;
  }
  .brand-dot {
    width: 34px;
    height: 34px;
    border-radius: 50%;
    background: var(--chalk);
  }
  .brand-name {
    font-family: "Barlow Condensed", "Arial Narrow", sans-serif;
    font-weight: 700;
    font-size: 56px;
    letter-spacing: 2px;
    color: var(--chalk);
    line-height: 1;
  }
  .benefits {
    position: absolute;
    left: 22px;
    top: 326px;
    margin: 0;
    padding: 0;
    list-style: none;
  }
  .benefit {
    display: flex;
    align-items: center;
    height: 70px;
  }
  .benefit-tick {
    width: 66px;
    height: 52px;
    flex: none;
  }
  .benefit-text {
    margin-left: 20px;
    font-family: "Barlow Condensed", "Arial Narrow", sans-serif;
    font-style: italic;
    font-weight: 700;
    font-size: 38px;
    color: var(--chalk);
    letter-spacing: 0.5px;
    white-space: nowrap;
  }
  .website {
    position: absolute;
    left: 104px;
    top: 712px;
    font-family: "Archivo", Arial, sans-serif;
    font-style: italic;
    font-weight: 800;
    font-size: 30px;
    color: var(--chalk);
    letter-spacing: 0.5px;
    line-height: 1;
  }
</style>
</head>
<body>
<main class="canvas">
  <section class="trailer-wrap">
    <div class="wall-texture" role="img" aria-label="Dunkelgraue Ziegelmauer im Graffiti-Stil als Hintergrund"></div>

    <div class="brand">
      <span class="brand-dot"></span>
      <span class="brand-name">FAHRSCHULE ZAP</span>
    </div>

    <ul class="benefits">
      <li class="benefit">
        <svg class="benefit-tick" viewBox="0 0 66 52" aria-hidden="true"><path d="M4 30 L22 46 L62 4" fill="none" stroke="var(--chalk-dim)" stroke-width="8" stroke-linecap="round" stroke-linejoin="round"/></svg>
        <span class="benefit-text">7 TAGE THEORIE INTENSIVKURS</span>
      </li>
      <li class="benefit">
        <svg class="benefit-tick" viewBox="0 0 66 52" aria-hidden="true"><path d="M4 30 L22 46 L62 4" fill="none" stroke="var(--chalk-dim)" stroke-width="8" stroke-linecap="round" stroke-linejoin="round"/></svg>
        <span class="benefit-text">TOP FAHRZEUGE</span>
      </li>
      <li class="benefit">
        <svg class="benefit-tick" viewBox="0 0 66 52" aria-hidden="true"><path d="M4 30 L22 46 L62 4" fill="none" stroke="var(--chalk-dim)" stroke-width="8" stroke-linecap="round" stroke-linejoin="round"/></svg>
        <span class="benefit-text">UNTERRICHT AUF ENGLISCH MÖGLICH</span>
      </li>
    </ul>

    <div class="website">WWW.FAHRSCHULE-ZAP.DE</div>
  </section>
</main>
</body>
</html>
```